Rack Card Design Project

We are a locally family owned public golf course. We would like to have a rack card designed that can be used for multiple applications. The colors in our logo are grey, blue, and white. Please use those in the card design. The company logo, contact information, address, and summer pricing should be included. I've included some pictures that may or may not be used. I'm also open to suggestions....use one photo, multiple photos, a stock photo or image representing golf etc.

```html
<!DOCTYPE html>
<html lang="en">
<head>
<meta charset="utf-8">
<title>Cedar Bend Golf Club – Rack Card</title>
<link href="https://fonts.googleapis.com/css2?family=Montserrat:wght@400;500;600;700;800&display=swap" rel="stylesheet">
<style>
  :root{
    --backdrop:#e6e7e8;
    --navy:#2a4160;
    --sky-blue:#93d3f2;
    --white:#ffffff;
    --swoosh-light:#f4f5f6;
    --swoosh-grey:#c9ccd0;
    --ink:#27405e;
  }
  *{margin:0;padding:0;box-sizing:border-box}
  html,body{width:1071px;height:1200px;overflow:hidden;background:var(--backdrop);font-family:"Montserrat",Arial,sans-serif}
  .card{position:absolute;top:188px;width:379px;height:823px;overflow:hidden;background:var(--navy)}
  .card--front{left:138px}
  .card--back{left:558px}
  .card svg.card-art{position:absolute;left:0;top:0;width:379px;height:823px}
  .brand-mark{position:absolute;display:flex;align-items:center;gap:6px;color:var(--white);font-weight:700;font-size:12px;letter-spacing:.5px;text-transform:uppercase;line-height:1.15}
  .brand-mark__dot{width:14px;height:14px;border-radius:50%;background:var(--white);flex:none}
  .club-name{position:absolute;left:0;width:100%;text-align:center;color:var(--white);font-weight:700;text-transform:uppercase;line-height:1.2}
  .card--front .club-name{top:660px;font-size:23px}
  .phone-divider{position:absolute;top:726px;left:0;width:100%;display:flex;align-items:center;justify-content:center;gap:6px}
  .phone-divider .rule{width:78px;height:1px;background:rgba(255,255,255,.5)}
  .phone-big{position:absolute;top:758px;width:100%;text-align:center;color:var(--white);font-weight:700;font-size:18px}
  .web{position:absolute;width:100%;text-align:center;color:var(--white);font-size:13px;letter-spacing:2.4px}
  .card--front .web{top:784px}
  .rates{position:absolute;left:32px;top:330px;width:314px;height:346px;background:var(--sky-blue);color:var(--ink)}
  .rates__title{position:absolute;left:26px;top:44px;width:261px;height:32px;background:var(--navy);color:var(--sky-blue);font-weight:800;font-size:29px;text-align:center;line-height:33px}
  .rates__season{position:absolute;left:0;top:83px;width:100%;text-align:center;font-weight:700;font-size:17px}
  .rates__season span{border-bottom:2px solid var(--ink);padding-bottom:1px}
  .rates__group{position:absolute;left:34px;width:259px;font-size:13px}
  .rates__heading{font-weight:700;font-size:14px;margin-bottom:6px}
  .rate-row{display:flex;align-items:baseline;height:21px}
  .rate-row .leader{flex:1;border-bottom:1px dashed var(--ink);margin:0 4px;transform:translateY(-3px);opacity:.7}
  .rate-row--bold .label{font-weight:700;font-size:14px}
  .kids{position:absolute;left:32px;top:258px;width:250px;height:50px;border:2px solid var(--navy);text-align:center;font-size:16px;line-height:20px;padding-top:3px}
  .kids strong{font-weight:700}
  .lunch{position:absolute;top:322px;width:100%;text-align:center;font-size:13px}
  .card--back .club-name{top:692px;font-size:18.5px}
  .contact-line{position:absolute;width:100%;display:flex;justify-content:center;align-items:center;gap:5px;color:var(--white)}
  .contact-line--address{top:741px;font-size:12px}
  .contact-line--phone{top:760px;font-size:16px;font-weight:700}
  .contact-line--web{top:781px;font-size:12.5px;letter-spacing:2px}
</style>
</head>
<body>

<!-- Front -->
<section class="card card--front">
  <svg class="card-art" viewBox="0 0 379 823">
    <defs>
      <linearGradient id="frontPhoto" x1="0" y1="0" x2="0" y2="1">
        <stop offset="0" stop-color="#3d9ee8"/>
        <stop offset=".55" stop-color="#cfe6f6"/>
        <stop offset=".72" stop-color="#8fc560"/>
        <stop offset="1" stop-color="#6aa534"/>
      </linearGradient>
      <linearGradient id="swoosh" x1="0" y1="0" x2="0" y2="1">
        <stop offset="0" stop-color="#ffffff"/>
        <stop offset="1" stop-color="#c9ccd0"/>
      </linearGradient>
    </defs>
    <rect width="379" height="823" fill="var(--navy)"/>
    <path d="M0 560 Q190 650 379 560 V640 H0Z" fill="url(#swoosh)"/>
    <path d="M0 0 H379 V560 Q190 630 0 562 Z" fill="url(#frontPhoto)" role="img" aria-label="Golfer in white cap and shirt finishing a drive on a green fairway under a blue sky"/>
    <path d="M0 604 Q190 668 379 600 V823 H0Z" fill="var(--navy)"/>
  </svg>
  <div class="brand-mark" style="left:214px;top:322px"><span class="brand-mark__dot"></span><span>Cedar Bend<br>Golf Club</span></div>
  <h1 class="club-name">The Greens of<br>Cedar Bend Golf Club</h1>
  <div class="phone-divider">
    <span class="rule"></span>
    <svg width="24" height="24" viewBox="0 0 24 24"><circle cx="12" cy="12" r="11" fill="none" stroke="#fff" stroke-width="1.2"/><path d="M8.5 6.5l2 2.2-1.1 1.4c.7 1.6 1.9 2.8 3.5 3.5l1.4-1.1 2.2 2-1.2 1.8c-3.8-.4-7.2-3.8-7.6-7.6z" fill="#fff"/></svg>
    <span class="rule"></span>
  </div>
  <p class="phone-big">555-204-7381</p>
  <p class="web">www.cedarbendgc.com</p>
</section>

<!-- Back -->
<section class="card card--back">
  <svg class="card-art" viewBox="0 0 379 823">
    <defs>
      <linearGradient id="backPhoto" x1="0" y1="0" x2="0" y2="1">
        <stop offset="0" stop-color="#8ec4e6"/>
        <stop offset=".45" stop-color="#e3eef3"/>
        <stop offset=".6" stop-color="#7fbf3e"/>
        <stop offset="1" stop-color="#4f9a2a"/>
      </linearGradient>
      <linearGradient id="swoosh2" x1="0" y1="0" x2="0" y2="1">
        <stop offset="0" stop-color="#ffffff"/>
        <stop offset="1" stop-color="#c9ccd0"/>
      </linearGradient>
    </defs>
    <rect width="379" height="823" fill="var(--navy)"/>
    <path d="M0 270 Q190 330 379 270 V330 H0Z" fill="url(#swoosh2)"/>
    <path d="M0 0 H379 V272 Q190 320 0 292 Z" fill="url(#backPhoto)" role="img" aria-label="Golf bag full of clubs on a sunny course with palm trees and a flag"/>
    <path d="M0 312 Q190 360 379 300 V823 H0Z" fill="var(--navy)"/>
  </svg>
  <div class="brand-mark" style="left:226px;top:64px"><span class="brand-mark__dot"></span><span>Cedar Bend<br>Golf Club</span></div>

  <div class="rates">
    <h2 class="rates__title">SUMMER RATES</h2>
    <p class="rates__season"><span>MAY 1 – SEPTEMBER 30</span></p>
    <div class="rates__group" style="top:114px">
      <p class="rates__heading">18 Holes With Cart</p>
      <div class="rate-row"><span class="label">7AM – 11AM</span><span class="leader"></span><span>$24</span></div>
      <div class="rate-row"><span class="label">11AM – 3PM</span><span class="leader"></span><span>$19</span></div>
      <div class="rate-row"><span class="label">3PM – Close</span><span class="leader"></span><span>$15</span></div>
    </div>
    <div class="rates__group" style="top:206px">
      <div class="rate-row rate-row--bold"><span class="label">9 Holes With Cart</span><span class="leader"></span><span>$15</span></div>
      <div class="rate-row rate-row--bold"><span class="label">Walking</span><span class="leader"></span><span>$12</span></div>
    </div>
    <div class="kids">CHILDREN 15 AND UNDER<br><strong>FREE WITH PAID ADULT</strong></div>
    <p class="lunch">Lunch Available Daily 10AM – 3PM</p>
  </div>

  <h1 class="club-name">The Greens of<br>Cedar Bend Golf Club</h1>
  <p class="contact-line contact-line--address">
    <svg width="10" height="14" viewBox="0 0 10 14"><path d="M5 0a5 5 0 0 0-5 5c0 3.5 5 9 5 9s5-5.5 5-9a5 5 0 0 0-5-5zm0 7a2 2 0 1 1 0-4 2 2 0 0 1 0 4z" fill="#fff"/></svg>
    4410 SW Heron Lake Rd Palm City, FL 34990
  </p>
  <p class="contact-line contact-line--phone">
    <svg width="10" height="14" viewBox="0 0 10 14"><path d="M3 0l2 3.5-1.5 1.3c.3 1.8 1 3.2 2 4.4l1.8-.6L9.5 12 8 14C3 12.5.5 6 2 .8z" fill="#fff"/></svg>
    555-204-7381
  </p>
  <p class="contact-line contact-line--web">
    <svg width="12" height="12" viewBox="0 0 12 12"><g fill="none" stroke="#fff" stroke-width=".9"><circle cx="6" cy="6" r="5.3"/><ellipse cx="6" cy="6" rx="2.3" ry="5.3"/><path d="M.7 6h10.6M1.6 3.2h8.8M1.6 8.8h8.8"/></g></svg>
    www.cedarbendgc.com
  </p>
</section>

</body>
</html>
```